Copper Field Agency Website - Wordpress Web UPDATED BRIEF

FINAL LOGO UPLOADED - please look to this as reference for how we would like the site to look and feel.

We are a digital marketing agency - looking to have a new website built. We are looking for a simple one page feel of site that will allow us to grow it later. (Feel free to take some liberties with that if your imagination veers off) Must be very, playful, bold, sleek and easily integrate video. Wordpress only.

Overview:

Copper Field is a creative constellation. We are built on what's great about the shared economy. With access to thousands of content creators, designers, technicians, writers, strategists and other creatives around the world, we are built differently than a traditional “brick and mortar” Marketing Agency. We provide the traditional services our clients have come to expect, without the “5X factor” of covering the overhead common in the old agency model. We believe even better work can be created in collaboration with our clients and by passing those savings back to them for their use. Our clients pay for our art, our work and our passion –not our furniture.

"Copper Field, Let's Build Together"

Target Market(s)

companies looking for creative agency help, video production, creative consulting and coaching

Industry/Entity Type

Digital Marketing

Coding

Coded - Design and coding required

Number of Pages Required

1 page

Font styles to use
Sans Serif

Colors
3277b5
33a6d7
ec1f27

Requirements
Must have
• Wordpress design is a must. Looking for a one sheet homepage - with sections that are all on the main front page. We will have videos to embed, and should be able to have client logos and easy access to show a variety of our creative work.
• Please look to the logo for how we would like the site to feel.
• Please think "icon process flow" instead of blocks of text (which we used to have). Use the text to explain what the process flow should represent - don't actually copy paste the text but show it visually in icons.
Nice to have
• innovation around how we show video content. solid colors complementary to our palette and aesthetic.
Should not have
• Standard HTML coding

```html
<!DOCTYPE html>
<html lang="en">
<head>
<meta charset="utf-8">
<title>Copper Field Agency</title>
<link href="https://fonts.googleapis.com/css2?family=Open+Sans:wght@400;600;700;800&display=swap" rel="stylesheet">
<style>
:root{
  --blue:#3277b5;
  --sky:#33a6d7;
  --red:#ec1f27;
  --ink:#2b2b2b;
  --muted:#6b6b6b;
  --light:#f3f3f3;
  --footer:#2a2a2a;
  --white:#ffffff;
}
*{margin:0;padding:0;box-sizing:border-box}
html,body{width:1200px;height:3776px;overflow:hidden}
body{position:relative;font-family:"Open Sans",Arial,sans-serif;color:var(--ink);background:var(--white)}
.abs{position:absolute}
.btn{display:inline-block;background:var(--red);color:var(--white);font-weight:700;font-size:15px;padding:11px 24px;border-radius:22px;text-transform:uppercase;letter-spacing:.5px}
.section-title{position:absolute;left:0;width:1200px;text-align:center;font-weight:700;font-size:40px;letter-spacing:1px;color:var(--ink)}

/* hero */
.hero{left:0;top:0;width:1200px;height:660px;background:linear-gradient(110deg,#0d1b2e 0%,#1d3552 38%,#3a4f68 62%,#1a2636 100%)}
.hero-photo{left:0;top:0;width:1200px;height:660px}
.logo-badge{width:112px;height:112px;border-radius:50%;background:var(--white);border:5px solid var(--blue);display:flex;align-items:center;justify-content:center;text-align:center;font-weight:800;font-size:17px;line-height:1.1;color:var(--blue)}
.hero .logo-badge{left:44px;top:16px}
.nav{right:40px;top:58px;display:flex;gap:22px;font-size:14px;font-weight:700;color:var(--white);text-transform:uppercase}
.nav .active{color:var(--sky)}
.hero-title{left:110px;top:236px;font-size:66px;font-weight:800;color:var(--white);letter-spacing:1px}
.hero-sub{left:112px;top:328px;font-size:24px;font-weight:600;color:var(--white)}
.hero .btn{left:112px;top:392px}
.arrow{font-size:34px;color:var(--white);font-weight:300}

/* about */
.about-title{left:110px;top:724px;font-size:40px;font-weight:700}
.about-text{left:110px;top:800px;width:470px;font-size:14px;line-height:1.75;color:var(--muted)}
.about .btn{left:110px;top:1010px}
.about-media{left:640px;top:748px;width:448px;height:300px;background:linear-gradient(120deg,#b7c3cf,#e9edf1 50%,#9fb1c2)}
.play{width:60px;height:60px;border-radius:50%;background:var(--ink);display:flex;align-items:center;justify-content:center}

/* services */
.services{left:0;top:1160px;width:1200px;height:660px;background:linear-gradient(135deg,#e6e8ea,#f4f4f4 45%,#dcdfe2)}
.svc-label{position:absolute;font-size:14px;font-weight:700;text-transform:uppercase;color:var(--ink)}

/* clients */
.client{top:1996px;width:200px;text-align:center;font-size:38px;font-weight:700;color:#9a9a9a}
.dots{left:576px;top:2096px;display:flex;gap:8px}
.dots span{width:10px;height:10px;border-radius:50%;background:#bbb}
.dots span:first-child{background:var(--blue)}

/* testimonials */
.testimonials{left:0;top:2204px;width:1200px;height:400px;background:var(--blue)}
.quote-box{left:160px;top:2296px;width:910px;height:128px;border:2px solid rgba(255,255,255,.6)}
.quote-text{left:240px;top:2330px;width:720px;text-align:center;font-size:15px;line-height:1.7;color:var(--white)}
.qmark{font-size:60px;font-weight:800;color:var(--white);line-height:1}
.avatar{left:568px;top:2432px;width:64px;height:64px;border-radius:50%;background:linear-gradient(135deg,#c9a98a,#6d5444)}
.person{left:0;width:1200px;text-align:center;color:var(--white)}

/* gallery */
.tile{position:absolute}

/* footer */
.footer{left:0;top:3360px;width:1200px;height:416px;background:var(--footer)}
.foot-col{top:3468px;color:var(--white)}
.foot-col h4{font-size:14px;font-weight:700;text-transform:uppercase;margin-bottom:14px}
.foot-col li{list-style:none;font-size:13px;line-height:1.65;color:#d0d0d0}
.ico{display:inline-block;width:12px;height:12px;border-radius:50%;background:var(--sky);margin-right:10px;vertical-align:-1px}
.news-input{width:270px;height:36px;border:1px solid #777;border-radius:4px;font-size:13px;color:#bbb;padding:9px 12px;margin-bottom:14px}
.copyright{left:0;top:3730px;width:1200px;text-align:center;font-size:12px;color:#bdbdbd}
</style>
</head>
<body>

<!-- HERO -->
<section class="abs hero">
  <div class="abs hero-photo" role="img" aria-label="Woman working at a desk with computer screens in a dim office"></div>
  <div class="abs logo-badge">Copper<br>Field</div>
  <nav class="abs nav">
    <span class="active">Home</span><span>About Us</span><span>Services</span><span>Our Clients</span><span>Testimonials</span><span>Gallery</span><span>Contact Us</span>
  </nav>
  <span class="abs arrow" style="left:26px;top:300px">&#8249;</span>
  <span class="abs arrow" style="right:26px;top:300px">&#8250;</span>
  <h1 class="abs hero-title">COPPER FIELD</h1>
  <p class="abs hero-sub">We are a digital marketing agency</p>
  <span class="abs btn">Read More</span>
</section>
<svg class="abs" style="left:0;top:560px" width="1200" height="120" viewBox="0 0 1200 120">
  <path d="M0 40 Q600 110 1200 40 L1200 120 L0 120 Z" fill="#fff"/>
  <path d="M0 52 Q600 104 1200 52" fill="none" stroke="#ec1f27" stroke-width="6"/>
  <path d="M0 62 Q600 112 1200 62" fill="none" stroke="#3277b5" stroke-width="4"/>
</svg>

<!-- ABOUT -->
<section class="about">
  <h2 class="abs about-title">ABOUT US</h2>
  <p class="abs about-text">Copper Field is a creative constellation. We are built on what's great about the shared economy. With access to thousands of content creators, designers, technicians, writers, strategists and other creatives around the world, we are built differently than a traditional "brick and mortar" Marketing Agency. We provide the traditional services our clients have come to expect, without the "5X factor" of covering the overhead common in the old agency model.</p>
  <span class="abs btn">Read More</span>
  <div class="abs about-media" role="img" aria-label="Woman at a desktop monitor showing marketing charts"></div>
  <div class="abs play" style="left:834px;top:868px">
    <svg width="22" height="22" viewBox="0 0 22 22"><path d="M6 3 L19 11 L6 19 Z" fill="#fff"/></svg>
  </div>
</section>

<!-- SERVICES -->
<section class="abs services" role="img" aria-label="Faded team meeting around a laptop"></section>
<svg class="abs" style="left:0;top:1160px" width="1200" height="20" viewBox="0 0 1200 20">
  <path d="M0 0 Q600 24 1200 0" fill="none" stroke="#fff" stroke-width="6"/>
</svg>
<h2 class="section-title" style="top:1232px">OUR SERVICES</h2>
<svg class="abs" style="left:0;top:1320px" width="1200" height="440" viewBox="0 0 1200 440">
  <circle cx="600" cy="208" r="150" fill="none" stroke="#7a7a7a" stroke-width="2" stroke-dasharray="4 6"/>
  <circle cx="600" cy="208" r="80" fill="#fff" stroke="#3277b5" stroke-width="8"/>
  <text x="600" y="202" text-anchor="middle" font-family="Open Sans, sans-serif" font-weight="800" font-size="18" fill="#3277b5">Copper</text>
  <text x="600" y="224" text-anchor="middle" font-family="Open Sans, sans-serif" font-weight="800" font-size="18" fill="#3277b5">Field</text>
  <!-- play tile -->
  <rect x="496" y="186" width="44" height="44" rx="6" fill="#fff" stroke="#3277b5" stroke-width="2"/>
  <path d="M512 197 L528 208 L512 219 Z" fill="#3277b5"/>
  <g fill="#fff" stroke="#555" stroke-width="2">
    <circle cx="600" cy="58" r="24"/>
    <circle cx="728" cy="130" r="24"/>
    <circle cx="748" cy="232" r="24"/>
    <circle cx="648" cy="350" r="24"/>
    <circle cx="512" cy="330" r="24"/>
    <circle cx="452" cy="208" r="24"/>
    <circle cx="488" cy="108" r="24"/>
  </g>
  <g fill="none" stroke="#3277b5" stroke-width="2.5" stroke-linecap="round">
    <circle cx="597" cy="55" r="8"/><path d="M603 61 L610 68"/>
    <path d="M718 138 L728 122 L738 138 Z"/>
    <rect x="738" y="224" width="20" height="16"/><path d="M738 230 H758"/>
    <path d="M638 344 H658 M638 350 H658 M638 356 H652"/>
    <rect x="502" y="322" width="18" height="14"/><path d="M520 326 L526 322 V336 L520 332"/>
    <path d="M442 214 V202 L458 196 V220 L442 214"/>
    <circle cx="488" cy="102" r="5"/><path d="M478 120 Q488 106 498 120"/>
  </g>
</svg>
<span class="svc-label" style="left:560px;top:1324px">Discovery</span>
<span class="svc-label" style="left:768px;top:1442px">Strategy</span>
<span class="svc-label" style="left:788px;top:1544px">Project Management</span>
<span class="svc-label" style="left:688px;top:1662px">Content</span>
<span class="svc-label" style="left:382px;top:1642px">Production</span>
<span class="svc-label" style="left:336px;top:1520px">Paid Media</span>
<span class="svc-label" style="left:380px;top:1406px">Coaching</span>

<!-- CLIENTS -->
<h2 class="section-title" style="top:1908px">OUR CLIENTS</h2>
<div class="abs client" style="left:110px">Northwind</div>
<div class="abs client" style="left:350px">Vantage</div>
<div class="abs client" style="left:600px">Keystone</div>
<div class="abs client" style="left:840px">Bluepeak</div>
<div class="abs dots"><span></span><span></span><span></span></div>

<!-- TESTIMONIALS -->
<section class="abs testimonials"></section>
<h2 class="section-title" style="top:2270px;color:#fff;background:var(--blue);width:300px;left:450px">TESTIMONIALS</h2>
<div class="abs quote-box"></div>
<span class="abs qmark" style="left:178px;top:2318px">&ldquo;</span>
<span class="abs qmark" style="left:1012px;top:2370px">&rdquo;</span>
<p class="abs quote-text">Copper Field is proving to be a leader in the creative consulting industry and we look forward to collaborating with them again in the future.</p>
<span class="abs arrow" style="left:56px;top:2352px">&#8249;</span>
<span class="abs arrow" style="right:56px;top:2352px">&#8250;</span>
<div class="abs avatar" role="img" aria-label="Client portrait"></div>
<div class="abs person" style="top:2508px;font-size:15px;font-weight:700">Marla Quinn</div>
<div class="abs person" style="top:2530px;font-size:12px">Harbor Stage</div>

<!-- GALLERY -->
<h2 class="section-title" style="top:2724px">GALLERY</h2>
<div class="tile" style="left:108px;top:2812px;width:232px;height:168px;background:linear-gradient(135deg,#c7b6a6,#7d6a5c)" role="img" aria-label="Team reviewing work at a table"></div>
<div class="tile" style="left:348px;top:2812px;width:240px;height:224px;background:linear-gradient(135deg,#dfe4ea,#a4b3c4)" role="img" aria-label="Woman holding a laptop in an office"></div>
<div class="tile" style="left:598px;top:2812px;width:234px;height:168px;background:linear-gradient(135deg,#ece9e4,#b8aca0)" role="img" aria-label="Women working together at a desk"></div>
<div class="tile" style="left:842px;top:2812px;width:246px;height:168px;background:linear-gradient(135deg,#b46a52,#d8c7b8)" role="img" aria-label="Woman on a laptop by a brick wall"></div>
<div class="tile" style="left:108px;top:2988px;width:232px;height:260px;background:linear-gradient(135deg,#c9a76a,#7a6a58)" role="img" aria-label="Workers in hard hats on site"></div>
<div class="tile" style="left:348px;top:3044px;width:240px;height:204px;background:linear-gradient(135deg,#a66a50,#d9cdc2)" role="img" aria-label="Woman smiling at a laptop"></div>
<div class="tile" style="left:598px;top:2988px;width:234px;height:260px;background:linear-gradient(135deg,#e8ecef,#9fb0bf)" role="img" aria-label="Colleagues discussing at a computer"></div>
<div class="tile" style="left:842px;top:2988px;width:246px;height:260px;background:linear-gradient(135deg,#b5644c,#e3dbd2)" role="img" aria-label="Two colleagues with a tablet"></div>

<!-- FOOTER -->
<section class="abs footer"></section>
<svg class="abs" style="left:0;top:3320px" width="1200" height="60" viewBox="0 0 1200 60">
  <path d="M0 40 Q600 0 1200 40 L1200 60 L0 60 Z" fill="#2a2a2a"/>
  <path d="M0 36 Q600 -4 1200 36" fill="none" stroke="#ec1f27" stroke-width="5"/>
</svg>
<div class="abs logo-badge" style="left:544px;top:3322px;width:112px;height:112px">Copper<br>Field</div>
<div class="abs foot-col" style="left:110px">
  <h4>Site Links</h4>
  <ul><li>Home</li><li>About Us</li><li>Services</li><li>Our Clients</li><li>Testimonials</li><li>Gallery</li><li>Contact Us</li></ul>
</div>
<div class="abs foot-col" style="left:308px">
  <h4>Contact Us</h4>
  <ul>
    <li><span class="ico"></span>235, Sed ut perspiciatis<br><span style="margin-left:22px">unde omnis iste natus</span></li>
    <li><span class="ico"></span>555 0142 300</li>
    <li><span class="ico"></span>info@copperfield-agency.com</li>
  </ul>
</div>
<div class="abs foot-col" style="left:592px">
  <h4>Follow Us</h4>
  <ul><li><span class="ico"></span>Social Feed</li><li><span class="ico"></span>Microblog</li><li><span class="ico"></span>Photo Stream</li></ul>
</div>
<div class="abs foot-col" style="left:812px">
  <h4>Newsletter</h4>
  <div class="news-input">Enter Your Email</div>
  <span class="btn" style="font-size:12px;padding:7px 16px">Submit</span>
</div>
<div class="abs copyright">&copy; 2019 Copper Field. All Rights Reserved.</div>

</body>
</html>
```